A Modern & Sleek "Coming Soon" Page for an A.I Recruiting App

For the “Coming Soon” website, a simple background with no people in it. I've attached an A.I image of what the page should generally look like.

- A single mobile phone as the main focus where the user actually clicks on the, “notify me” button (after entering their email address).
- In the background where the pillars/columns are seen in the example, should be subtle pad locks that are in their opened position with a key inside the lock. I've attached images to try to illustrate this idea, but they are far away in style from what I'm looking for.

SLOGAN: Unlocking the power of meaningful connections
LOGO/TITLE: Should be the name as shown in image with only the name "KelvoLink" on it
COLORS: Purplish/blue hues. Should not be too feminine
NOTE: The user should only click once when signing up/entering their email.

Product: A recruiting platform that matches employers/employees with A.I. and prioritizing cultural fit/values system before skills. The industry we are tackling first is the caregiving industry (nannies, tutors, elderly). All users will be background screened and that info lives on the blockchain. All users will have the option to review and be reviewed/rated.

```html
<!DOCTYPE html>
<html lang="en">
<head>
<meta charset="UTF-8">
<title>KelvoLink – Coming Soon</title>
<link rel="stylesheet" href="https://fonts.googleapis.com/css2?family=Roboto:wght@300;400;500;700&display=swap">
<style>
  :root {
    --bg-deep: #1c0638;
    --bg-mid: #4a148c;
    --bg-glow: #8a3ad6;
    --magenta: #b40f84;
    --magenta-soft: #a8237f;
    --footer: #b10f80;
    --white: #ffffff;
    --ink: #1a1a1a;
    --muted: #666666;
    --lock-pink: #f6a6e6;
    --lock-violet: #7b3ce0;
  }
  * { margin: 0; padding: 0; box-sizing: border-box; }
  html, body { width: 1200px; height: 662px; overflow: hidden; }
  body { font-family: "Roboto", Arial, sans-serif; color: var(--white); }

  .page {
    position: relative;
    width: 1200px;
    height: 662px;
    overflow: hidden;
    background:
      radial-gradient(circle at 1150px 180px, rgba(200,120,255,0.55), transparent 260px),
      radial-gradient(circle at 700px 330px, rgba(150,80,230,0.45), transparent 320px),
      radial-gradient(circle at 1100px 480px, rgba(160,90,240,0.5), transparent 240px),
      radial-gradient(circle at 60px 40px, var(--bg-deep), transparent 320px),
      linear-gradient(135deg, #2a0a55 0%, var(--bg-mid) 45%, #6a26b8 100%);
  }

  .corner-arc {
    position: absolute;
    left: -170px; top: -170px;
    width: 216px; height: 216px;
    border: 2px solid #c2308f;
    border-radius: 50%;
  }
  .edge-arc {
    position: absolute;
    left: 1166px; top: 160px;
    width: 340px; height: 340px;
    border: 3px solid var(--white);
    border-radius: 50%;
  }

  .lock-art {
    position: absolute;
    border-radius: 45% 45% 50% 50%;
    background: radial-gradient(circle at 62% 62%, var(--lock-pink) 0%, #e58ad8 45%, var(--lock-violet) 100%);
    opacity: 0.9;
  }
  .lock-top      { left: 424px;  top: 20px;  width: 101px; height: 116px; }
  .lock-right    { left: 1082px; top: 102px; width: 90px;  height: 102px; }
  .lock-left     { left: 6px;    top: 412px; width: 80px;  height: 92px; }
  .lock-center   { left: 463px;  top: 438px; width: 141px; height: 161px; }
  .lock-bottom   { left: 1056px; top: 496px; width: 90px;  height: 102px; }

  .brand {
    position: absolute;
    left: 144px; top: 24px;
    font-weight: 300;
    font-size: 26px;
    letter-spacing: 3px;
    text-transform: uppercase;
    color: var(--white);
  }

  .hero { position: absolute; left: 144px; top: 162px; }
  .hero-title {
    font-size: 37px;
    font-weight: 700;
    line-height: 60px;
    font-family: "Roboto", Arial, sans-serif;
  }
  .hero-lead {
    margin-top: 22px;
    font-size: 17.5px;
    font-weight: 500;
  }
  .actions { display: flex; gap: 17px; margin-top: 37px; }
  .btn {
    display: inline-flex; align-items: center; gap: 8px;
    height: 46px;
    padding: 0 22px;
    border: 1.5px solid var(--white);
    border-radius: 5px;
    font-size: 16px; font-weight: 700;
    color: var(--white);
    text-decoration: none;
  }
  .btn svg { width: 15px; height: 15px; }

  .showcase { position: absolute; left: 659px; top: 112px; width: 396px; height: 396px; }
  .ring {
    position: absolute; inset: 0;
    border-radius: 50%;
    background: rgba(255,255,255,0.35);
    box-shadow: 0 0 0 3px rgba(255,255,255,0.2);
  }
  .disc {
    position: absolute; inset: 18px;
    border-radius: 50%;
    background: var(--magenta);
  }
  .dot {
    position: absolute; width: 30px; height: 30px; border-radius: 50%;
    background: rgba(200,30,130,0.8);
  }
  .dot-a { left: 18px;  top: 42px; }
  .dot-b { left: 381px; top: 230px; }
  .dot-c { left: 44px;  top: 318px; }

  .phone {
    position: absolute;
    left: 760px; top: 50px;
    width: 194px; height: 377px;
    border-radius: 30px;
    background: #111;
    border: 2px solid #444;
    padding: 8px;
    box-shadow: 0 20px 30px rgba(60,0,40,0.45);
  }
  .phone-screen {
    position: relative;
    width: 100%; height: 100%;
    border-radius: 22px;
    background: var(--white);
    color: var(--ink);
    text-align: center;
  }
  .phone-notch {
    position: absolute; left: 50%; top: 0;
    width: 88px; height: 16px;
    transform: translateX(-50%);
    background: #111;
    border-radius: 0 0 12px 12px;
  }
  .phone-brand {
    position: absolute; top: 66px; left: 0; right: 0;
    font-weight: 300; font-size: 17px; letter-spacing: 1.5px;
    text-transform: uppercase; color: var(--magenta);
  }
  .phone-slogan {
    position: absolute; top: 153px; left: 12px; right: 12px;
    font-size: 8.5px; line-height: 13px; font-weight: 400;
  }
  .phone-btn {
    position: absolute; top: 278px; left: 23px; right: 23px;
    height: 34px; border-radius: 3px;
    background: var(--magenta-soft); color: var(--white);
    display: flex; align-items: center; justify-content: center; gap: 5px;
    font-size: 9.5px; font-weight: 500;
  }
  .phone-btn svg { width: 9px; height: 9px; }
  .phone-note {
    position: absolute; top: 328px; left: 14px; right: 14px;
    font-size: 6.5px; line-height: 13px; color: var(--muted);
  }

  .site-footer {
    position: absolute; left: 0; bottom: 0;
    width: 1200px; height: 47px;
    background: var(--footer);
    display: flex; align-items: center; justify-content: center;
    font-size: 13.5px;
  }
</style>
</head>
<body>
<main class="page">
  <div class="corner-arc"></div>
  <div class="edge-arc"></div>

  <div class="lock-art lock-top" role="img" aria-label="Open heart-shaped padlock with a key inside"></div>
  <div class="lock-art lock-right" role="img" aria-label="Open heart-shaped padlock with a key inside"></div>
  <div class="lock-art lock-left" role="img" aria-label="Open heart-shaped padlock with a key inside"></div>
  <div class="lock-art lock-center" role="img" aria-label="Open heart-shaped padlock with a key inside"></div>
  <div class="lock-art lock-bottom" role="img" aria-label="Open heart-shaped padlock with a key inside"></div>

  <header class="brand">KelvoLink</header>

  <section class="hero">
    <h1 class="hero-title">Unlocking The Power of<br>Meaningful Connections</h1>
    <p class="hero-lead">Lorem ipsum dolor sit amet, consectetur.</p>
    <div class="actions">
      <a class="btn" href="#">NOTIFY ME
        <svg viewBox="0 0 16 16"><circle cx="8" cy="8" r="8" fill="#fff"/><path d="M6.5 4.5 10 8l-3.5 3.5" stroke="#4a148c" stroke-width="2" fill="none"/></svg>
      </a>
      <a class="btn" href="#">SIGN UP
        <svg viewBox="0 0 16 16"><circle cx="8" cy="8" r="8" fill="#fff"/><path d="M6.5 4.5 10 8l-3.5 3.5" stroke="#4a148c" stroke-width="2" fill="none"/></svg>
      </a>
    </div>
  </section>

  <div class="showcase">
    <div class="ring"></div>
    <div class="disc"></div>
    <span class="dot dot-a"></span>
    <span class="dot dot-b"></span>
    <span class="dot dot-c"></span>
  </div>

  <div class="phone">
    <div class="phone-screen">
      <div class="phone-notch"></div>
      <div class="phone-brand">KelvoLink</div>
      <p class="phone-slogan">Unlocking The Power Of Meaningful Connections</p>
      <div class="phone-btn">NOTIFY ME
        <svg viewBox="0 0 16 16"><circle cx="8" cy="8" r="8" fill="#fff"/><path d="M6.5 4.5 10 8l-3.5 3.5" stroke="#a8237f" stroke-width="2.2" fill="none"/></svg>
      </div>
      <p class="phone-note">Lorem ipsum dolor sit amet,consectetur<br>adipiscing elit, sed do eiusmod.</p>
    </div>
  </div>

  <footer class="site-footer">Copyright © 2024 KelvoLink - All Rights Reserved.</footer>
</main>
</body>
</html>
```